Graphics for New Online Software

Looking at a designer to design a UI/UX Interface for an Online Events Platform (just JPEG) and some corresponding images for a website content (i.e. features etc)

Deliverables:
1x User Interface Design for the Platform (refer to attachment)
5-6x Feature Listing Images (refer to attachment)

Target Market(s)

Technology, Online Users Etc

Industry/Entity Type

Software Developer

Number of Pages Required

1 page

Font styles to use
Sans Serif

Colors
34a7d8
0493ce
3176b5
85acd3

Requirements
Must have
• Looks like a well built software - examples:
https://gravelmoor.io/
https://quintaro.com/

All the images should look very professional, as though you are using it on the online platform itself.
Nice to have
• Refer to attached "Feature Listing" and Logo

```html
<!DOCTYPE html>
<html lang="en">
<head>
<meta charset="utf-8">
<title>Venuro – Event Platform UI</title>
<link href="https://fonts.googleapis.com/css2?family=Poppins:wght@400;500;600&display=swap" rel="stylesheet">
<style>
:root{
  --page:#eef0f4;
  --panel:#ffffff;
  --ink:#1d1f2b;
  --muted:#4a4d5c;
  --blue:#2b3cf6;
  --blue-2:#2f6bf2;
  --sky:#46c9ff;
  --chip:#2f7df0;
  --chip-2:#3aa2f5;
  --line:#e6e8ee;
  --field:#eceef2;
  --main:#f0f1f4;
}
*{box-sizing:border-box;margin:0;padding:0}
html,body{width:1200px;height:2394px;overflow:hidden}
body{background:var(--page);font-family:'Poppins',sans-serif;color:var(--ink);position:relative}
.screen{position:absolute;left:39px;width:1122px;background:var(--main);box-shadow:0 6px 24px rgba(40,50,90,.12)}
.screen--speakers{top:72px;height:660px}
.screen--stage{top:792px;height:870px}
.screen--breakouts{top:1715px;height:609px}

.sidebar{position:absolute;left:0;top:0;bottom:0;width:204px;border-top-left-radius:20px;
  background:linear-gradient(170deg,var(--blue) 0%,var(--blue-2) 35%,var(--sky) 70%,var(--blue-2) 100%)}
.screen--speakers .sidebar{background:linear-gradient(172deg,var(--blue) 0%,var(--blue-2) 45%,var(--sky) 100%)}
.brand{position:absolute;left:20px;top:44px;color:#fff;font-weight:600;font-size:26px;letter-spacing:-.5px;display:flex;align-items:center;gap:8px}
.brand-dot{width:12px;height:12px;border-radius:50%;background:#fff}
.nav{position:absolute;left:38px;top:135px;right:0;list-style:none}
.nav li{height:50.4px;display:flex;align-items:center;gap:12px;padding-left:12px;color:#fff;font-size:13.5px;font-weight:500}
.nav li svg{width:20px;height:20px;flex:none}
.nav li.is-active{background:#fff;color:var(--ink);border-radius:18px 0 0 18px;height:36px;margin:7px 0}
.nav li.is-active svg{stroke:var(--ink)}

.topbar{position:absolute;left:232px;right:0;top:0;height:68px;background:#fff;box-shadow:0 2px 8px rgba(0,0,0,.04)}
.search{position:absolute;left:20px;top:18px;width:327px;height:31px;border-radius:16px;background:var(--field);overflow:hidden}
.search span{position:absolute;left:14px;top:6px;font-size:12.5px;color:#555}
.search-btn{position:absolute;right:0;top:0;width:57px;height:31px;background:var(--blue);border-radius:0 16px 16px 0;display:flex;align-items:center;justify-content:center}
.duration{position:absolute;left:440px;top:18px;display:flex;align-items:center;gap:4px;font-size:15.5px;font-weight:500}
.duration .label{margin-right:8px}
.digit{width:36px;height:31px;background:linear-gradient(135deg,var(--chip),var(--chip-2));color:#fff;font-size:14px;display:flex;align-items:center;justify-content:center}
.colon{font-weight:600;padding:0 2px}
.icon-btn{position:absolute;top:20px;width:28px;height:28px;border-radius:50%;background:var(--field);display:flex;align-items:center;justify-content:center}
.avatar{border-radius:50%;background:radial-gradient(circle at 50% 40%,#c9a08a,#5a4638)}
.topbar .avatar{position:absolute;left:846px;top:14px;width:38px;height:38px}

.content{position:absolute;left:233px;width:862px;top:93px;background:var(--panel)}
.screen--speakers .content{height:518px}
.screen--stage .content{height:750px}
.screen--breakouts .content{height:468px}
.heading{position:absolute;font-size:28px;font-weight:500;left:26px}

.card{position:absolute;background:#fff;border-radius:10px;box-shadow:0 0 0 1px var(--line),0 3px 10px rgba(0,0,0,.05)}
.speaker{top:85px;width:247px;height:352px;text-align:center}
.speaker .avatar{width:96px;height:96px;margin:32px auto 0}
.speaker h3{font-size:19px;font-weight:400;margin-top:18px}
.speaker p{font-size:11.5px;line-height:21px;color:var(--muted);padding:0 22px;margin-top:6px}
.actions{display:flex;gap:8px;justify-content:center;margin-top:22px}
.actions span{width:41px;height:41px;border-radius:50%;background:linear-gradient(135deg,var(--blue-2),var(--chip-2));display:flex;align-items:center;justify-content:center}

.video-card{left:27px;top:86px;width:527px;height:316px}
.video{position:absolute;left:10px;top:10px;right:10px;bottom:14px;background:linear-gradient(160deg,#4a4f66,#1e2230 60%,#5c4a63);display:flex;align-items:center;justify-content:center}
.chat{left:574px;top:86px;width:268px;height:316px}
.tabs{position:absolute;left:574px;top:38px;width:268px;height:48px}
.tab-chat{position:absolute;left:17px;top:12px;font-size:20px;font-weight:500}
.tab-blue{position:absolute;left:90px;top:0;width:160px;height:48px;background:linear-gradient(90deg,var(--chip),var(--blue-2));transform:skewX(20deg);border-radius:4px 4px 0 0}
.tab-label{position:absolute;top:12px;color:#fff;font-size:20px;font-weight:500}
.msg{position:absolute;left:17px;right:12px;height:98px;display:flex;gap:14px;align-items:center}
.msg .avatar{width:52px;height:52px;flex:none}
.msg h4{font-size:13.5px;font-weight:400}
.msg p{font-size:10px;line-height:15px;color:var(--muted)}
.divider{position:absolute;left:12px;right:12px;border-top:1px dashed #bbb}
.agenda{left:27px;top:511px;width:816px;height:205px}
.agenda svg{position:absolute;left:32px;top:55px}
.agenda p{position:absolute;left:148px;right:30px;top:65px;font-size:13.5px;line-height:25px;color:#333}

.room{top:35px;width:380px;height:386px}
.room-head{position:absolute;left:8px;right:14px;top:22px;display:flex;justify-content:space-between;font-size:20px;font-weight:500}
.room-head small{font-size:17px}
.room-photo{position:absolute;left:11px;top:60px;width:360px;height:250px;background:linear-gradient(170deg,#c9ccd2,#7c8592 55%,#34373f)}
.room-time{position:absolute;left:0;right:0;top:328px;text-align:center;font-size:12.5px}
.room-link{position:absolute;left:0;right:0;top:347px;text-align:center;font-size:17.5px;font-weight:500;text-decoration:underline}
</style>
</head>
<body>

<!-- Speakers screen -->
<section class="screen screen--speakers">
  <aside class="sidebar">
    <div class="brand"><span class="brand-dot"></span>VENURO</div>
    <ul class="nav">
      <li class="is-active"><svg viewBox="0 0 24 24" fill="none" stroke="#fff" stroke-width="1.6"><circle cx="12" cy="12" r="9"/><path d="M12 11v6M12 7.5v.5"/></svg>Event Info</li>
      <li><svg viewBox="0 0 24 24" fill="none" stroke="#fff" stroke-width="1.6"><rect x="3" y="4" width="18" height="15"/><path d="M3 8h18M7 19l3-5 3 3 2-2 3 4"/></svg>Stage</li>
      <li><svg viewBox="0 0 24 24" fill="none" stroke="#fff" stroke-width="1.6"><path d="M4 9h4l5-4v14l-5-4H4z"/><path d="M16 9c1.5 1.5 1.5 4.5 0 6M19 7c3 3 3 7 0 10"/></svg>Breakouts</li>
      <li><svg viewBox="0 0 24 24" fill="none" stroke="#fff" stroke-width="1.6"><rect x="7" y="3" width="10" height="18" rx="1"/><circle cx="12" cy="13" r="2"/><path d="M10 7h4"/></svg>Virtual</li>
      <li><svg viewBox="0 0 24 24" fill="none" stroke="#fff" stroke-width="1.6"><circle cx="12" cy="5" r="2.5"/><path d="M4 11h16v3H4zM6 14v7M18 14v7M9 11V9h6v2"/></svg>Exhibition</li>
      <li><svg viewBox="0 0 24 24" fill="none" stroke="#fff" stroke-width="1.6"><circle cx="12" cy="5" r="2"/><path d="M9 11h6"/><circle cx="5" cy="16" r="1.6"/><circle cx="12" cy="16" r="1.6"/><circle cx="19" cy="16" r="1.6"/><path d="M3 21h4M10 21h4M17 21h4"/></svg>Booths</li>
      <li><svg viewBox="0 0 24 24" fill="none" stroke="#fff" stroke-width="1.6"><path d="M12 3l2.5 5 5.5.8-4 3.9.9 5.5L12 15.6 7.1 18.2 8 12.7 4 8.8 9.5 8z"/><path d="M10 19v3M14 19v3"/></svg>Rewards</li>
    </ul>
  </aside>
  <header class="topbar">
    <div class="search"><span>Search</span><div class="search-btn"><svg width="14" height="14" viewBox="0 0 24 24" fill="none" stroke="#fff" stroke-width="2.4"><circle cx="10" cy="10" r="6.5"/><path d="M15 15l5 5"/></svg></div></div>
    <div class="duration"><span class="label">Event Duration</span><span class="digit">12</span><span class="colon">:</span><span class="digit">10</span><span class="colon">:</span><span class="digit">00</span></div>
    <span class="icon-btn" style="left:755px"><svg width="15" height="15" viewBox="0 0 24 24" fill="none" stroke="var(--blue)" stroke-width="2"><path d="M6 16V11a6 6 0 0 1 12 0v5l2 2H4zM10 21h4"/></svg></span>
    <span class="icon-btn" style="left:800px"><svg width="15" height="15" viewBox="0 0 24 24" fill="none" stroke="var(--blue)" stroke-width="2"><rect x="3" y="6" width="18" height="12"/><path d="M3 6l9 7 9-7"/></svg></span>
    <span class="avatar" role="img" aria-label="User profile photo"></span>
  </header>
  <main class="content">
    <h2 class="heading" style="top:24px">Our Speakers</h2>
    <article class="card speaker" style="left:27px">
      <div class="avatar" role="img" aria-label="Portrait of John Smith"></div>
      <h3>John Smith</h3>
      <p>Nemo enim ipsam voluptatem quia voluptas sit aspernatur aut odit aut fugit, sed quia consequuntur magni dolores.</p>
      <div class="actions">
        <span><svg width="22" height="22" viewBox="0 0 24 24" fill="none" stroke="#fff" stroke-width="1.6"><circle cx="12" cy="12" r="9"/><path d="M12 11v6M12 7.5v.5"/></svg></span>
        <span><svg width="22" height="22" viewBox="0 0 24 24" fill="none" stroke="#fff" stroke-width="1.6"><circle cx="12" cy="5" r="2.5"/><path d="M4 11h16v3H4zM6 14v7M18 14v7M9 11V9h6v2"/></svg></span>
        <span><svg width="22" height="22" viewBox="0 0 24 24" fill="none" stroke="#fff" stroke-width="1.6"><path d="M4 9h4l5-4v14l-5-4H4z"/><path d="M16 9c1.5 1.5 1.5 4.5 0 6M19 7c3 3 3 7 0 10"/></svg></span>
      </div>
    </article>
    <article class="card speaker" style="left:302px">
      <div class="avatar" role="img" aria-label="Portrait of Riyan Smith"></div>
      <h3>Riyan Smith</h3>
      <p>Nemo enim ipsam voluptatem quia voluptas sit aspernatur aut odit aut fugit, sed quia consequuntur magni dolores.</p>
      <div class="actions">
        <span><svg width="22" height="22" viewBox="0 0 24 24" fill="none" stroke="#fff" stroke-width="1.6"><circle cx="12" cy="12" r="9"/><path d="M12 11v6M12 7.5v.5"/></svg></span>
        <span><svg width="22" height="22" viewBox="0 0 24 24" fill="none" stroke="#fff" stroke-width="1.6"><circle cx="12" cy="5" r="2.5"/><path d="M4 11h16v3H4zM6 14v7M18 14v7M9 11V9h6v2"/></svg></span>
        <span><svg width="22" height="22" viewBox="0 0 24 24" fill="none" stroke="#fff" stroke-width="1.6"><path d="M4 9h4l5-4v14l-5-4H4z"/><path d="M16 9c1.5 1.5 1.5 4.5 0 6M19 7c3 3 3 7 0 10"/></svg></span>
      </div>
    </article>
    <article class="card speaker" style="left:575px">
      <div class="avatar" role="img" aria-label="Portrait of Clara Thomas"></div>
      <h3>Clara Thomas</h3>
      <p>Nemo enim ipsam voluptatem quia voluptas sit aspernatur aut odit aut fugit, sed quia consequuntur magni dolores.</p>
      <div class="actions">
        <span><svg width="22" height="22" viewBox="0 0 24 24" fill="none" stroke="#fff" stroke-width="1.6"><circle cx="12" cy="12" r="9"/><path d="M12 11v6M12 7.5v.5"/></svg></span>
        <span><svg width="22" height="22" viewBox="0 0 24 24" fill="none" stroke="#fff" stroke-width="1.6"><circle cx="12" cy="5" r="2.5"/><path d="M4 11h16v3H4zM6 14v7M18 14v7M9 11V9h6v2"/></svg></span>
        <span><svg width="22" height="22" viewBox="0 0 24 24" fill="none" stroke="#fff" stroke-width="1.6"><path d="M4 9h4l5-4v14l-5-4H4z"/><path d="M16 9c1.5 1.5 1.5 4.5 0 6M19 7c3 3 3 7 0 10"/></svg></span>
      </div>
    </article>
  </main>
</section>

<!-- Stage screen -->
<section class="screen screen--stage">
  <aside class="sidebar">
    <div class="brand"><span class="brand-dot"></span>VENURO</div>
    <ul class="nav">
      <li><svg viewBox="0 0 24 24" fill="none" stroke="#fff" stroke-width="1.6"><circle cx="12" cy="12" r="9"/><path d="M12 11v6M12 7.5v.5"/></svg>Event Info</li>
      <li class="is-active"><svg viewBox="0 0 24 24" fill="none" stroke="#fff" stroke-width="1.6"><rect x="3" y="4" width="18" height="15"/><path d="M3 8h18M7 19l3-5 3 3 2-2 3 4"/></svg>Stage</li>
      <li><svg viewBox="0 0 24 24" fill="none" stroke="#fff" stroke-width="1.6"><path d="M4 9h4l5-4v14l-5-4H4z"/><path d="M16 9c1.5 1.5 1.5 4.5 0 6M19 7c3 3 3 7 0 10"/></svg>Breakouts</li>
      <li><svg viewBox="0 0 24 24" fill="none" stroke="#fff" stroke-width="1.6"><rect x="7" y="3" width="10" height="18" rx="1"/><circle cx="12" cy="13" r="2"/><path d="M10 7h4"/></svg>Virtual</li>
      <li><svg viewBox="0 0 24 24" fill="none" stroke="#fff" stroke-width="1.6"><circle cx="12" cy="5" r="2.5"/><path d="M4 11h16v3H4zM6 14v7M18 14v7M9 11V9h6v2"/></svg>Exhibition</li>
      <li><svg viewBox="0 0 24 24" fill="none" stroke="#fff" stroke-width="1.6"><circle cx="12" cy="5" r="2"/><path d="M9 11h6"/><circle cx="5" cy="16" r="1.6"/><circle cx="12" cy="16" r="1.6"/><circle cx="19" cy="16" r="1.6"/><path d="M3 21h4M10 21h4M17 21h4"/></svg>Booths</li>
      <li><svg viewBox="0 0 24 24" fill="none" stroke="#fff" stroke-width="1.6"><path d="M12 3l2.5 5 5.5.8-4 3.9.9 5.5L12 15.6 7.1 18.2 8 12.7 4 8.8 9.5 8z"/><path d="M10 19v3M14 19v3"/></svg>Rewards</li>
    </ul>
  </aside>
  <header class="topbar">
    <div class="search"><span>Search</span><div class="search-btn"><svg width="14" height="14" viewBox="0 0 24 24" fill="none" stroke="#fff" stroke-width="2.4"><circle cx="10" cy="10" r="6.5"/><path d="M15 15l5 5"/></svg></div></div>
    <div class="duration"><span class="label">Event Duration</span><span class="digit">12</span><span class="colon">:</span><span class="digit">10</span><span class="colon">:</span><span class="digit">00</span></div>
    <span class="icon-btn" style="left:755px"><svg width="15" height="15" viewBox="0 0 24 24" fill="none" stroke="var(--blue)" stroke-width="2"><path d="M6 16V11a6 6 0 0 1 12 0v5l2 2H4zM10 21h4"/></svg></span>
    <span class="icon-btn" style="left:800px"><svg width="15" height="15" viewBox="0 0 24 24" fill="none" stroke="var(--blue)" stroke-width="2"><rect x="3" y="6" width="18" height="12"/><path d="M3 6l9 7 9-7"/></svg></span>
    <span class="avatar" role="img" aria-label="User profile photo"></span>
  </header>
  <main class="content">
    <h2 class="heading" style="top:32px">Our Video</h2>
    <div class="card video-card">
      <div class="video" role="img" aria-label="Speaker at a podium addressing a conference audience">
        <svg width="58" height="58" viewBox="0 0 58 58"><circle cx="29" cy="29" r="26" fill="none" stroke="#fff" stroke-width="3"/><path d="M23 18l17 11-17 11z" fill="#fff"/></svg>
      </div>
    </div>
    <div class="tabs">
      <span class="tab-chat">Chat</span>
      <span class="tab-blue"></span>
      <span class="tab-label" style="left:102px">Q\A</span>
      <span class="tab-label" style="left:182px">Poll</span>
    </div>
    <div class="card chat">
      <div class="msg" style="top:0"><span class="avatar" role="img" aria-label="Attendee photo"></span><div><h4>Nemo enim ipsam</h4><p>Sed ut perspiciatis unde omnis iste natus error sit voluptatem</p></div></div>
      <div class="divider" style="top:114px"></div>
      <div class="msg" style="top:114px"><span class="avatar" role="img" aria-label="Attendee photo"></span><div><h4>Nemo enim ipsam</h4><p>Sed ut perspiciatis unde omnis iste natus error sit voluptatem</p></div></div>
      <div class="divider" style="top:212px"></div>
      <div class="msg" style="top:212px"><span class="avatar" role="img" aria-label="Attendee photo"></span><div><h4>Nemo enim ipsam</h4><p>Sed ut perspiciatis unde omnis iste natus error sit voluptatem</p></div></div>
    </div>
    <h2 class="heading" style="top:458px">Agenda/Programming</h2>
    <div class="card agenda">
      <svg width="90" height="95" viewBox="0 0 90 95" fill="none" stroke="url(#podium)" stroke-width="5" stroke-linecap="round" stroke-linejoin="round">
        <defs><linearGradient id="podium" x1="0" y1="0" x2="1" y2="1"><stop offset="0" stop-color="#2b3cf6"/><stop offset="1" stop-color="#46c9ff"/></linearGradient></defs>
        <circle cx="44" cy="14" r="11"/><path d="M26 42c0-10 8-16 18-16s18 6 18 16M4 42h82v12H4zM10 54l4 6h62l4-6M18 60v32M72 60v32M8 38V28"/>
      </svg>
      <p>Nemo enim ipsam voluptatem quia voluptas sit aspernatur aut odit aut fugit, sed quia consequuntur magni dolores eos qui ratione voluptatem sequi nesciunt. Neque porro quisquam est, qui dolorem ipsum quia dolor sit amet, consectetur, adipisci velit, sed quia non numquam</p>
    </div>
  </main>
</section>

<!-- Breakouts screen -->
<section class="screen screen--breakouts">
  <aside class="sidebar">
    <div class="brand"><span class="brand-dot"></span>VENURO</div>
    <ul class="nav">
      <li><svg viewBox="0 0 24 24" fill="none" stroke="#fff" stroke-width="1.6"><circle cx="12" cy="12" r="9"/><path d="M12 11v6M12 7.5v.5"/></svg>Event Info</li>
      <li><svg viewBox="0 0 24 24" fill="none" stroke="#fff" stroke-width="1.6"><rect x="3" y="4" width="18" height="15"/><path d="M3 8h18M7 19l3-5 3 3 2-2 3 4"/></svg>Stage</li>
      <li class="is-active"><svg viewBox="0 0 24 24" fill="none" stroke="#fff" stroke-width="1.6"><path d="M4 9h4l5-4v14l-5-4H4z"/><path d="M16 9c1.5 1.5 1.5 4.5 0 6M19 7c3 3 3 7 0 10"/></svg>Breakouts</li>
      <li><svg viewBox="0 0 24 24" fill="none" stroke="#fff" stroke-width="1.6"><rect x="7" y="3" width="10" height="18" rx="1"/><circle cx="12" cy="13" r="2"/><path d="M10 7h4"/></svg>Virtual</li>
      <li><svg viewBox="0 0 24 24" fill="none" stroke="#fff" stroke-width="1.6"><circle cx="12" cy="5" r="2.5"/><path d="M4 11h16v3H4zM6 14v7M18 14v7M9 11V9h6v2"/></svg>Exhibition</li>
      <li><svg viewBox="0 0 24 24" fill="none" stroke="#fff" stroke-width="1.6"><circle cx="12" cy="5" r="2"/><path d="M9 11h6"/><circle cx="5" cy="16" r="1.6"/><circle cx="12" cy="16" r="1.6"/><circle cx="19" cy="16" r="1.6"/><path d="M3 21h4M10 21h4M17 21h4"/></svg>Booths</li>
      <li><svg viewBox="0 0 24 24" fill="none" stroke="#fff" stroke-width="1.6"><path d="M12 3l2.5 5 5.5.8-4 3.9.9 5.5L12 15.6 7.1 18.2 8 12.7 4 8.8 9.5 8z"/><path d="M10 19v3M14 19v3"/></svg>Rewards</li>
    </ul>
  </aside>
  <header class="topbar">
    <div class="search"><span>Search</span><div class="search-btn"><svg width="14" height="14" viewBox="0 0 24 24" fill="none" stroke="#fff" stroke-width="2.4"><circle cx="10" cy="10" r="6.5"/><path d="M15 15l5 5"/></svg></div></div>
    <div class="duration"><span class="label">Event Duration</span><span class="digit">12</span><span class="colon">:</span><span class="digit">10</span><span class="colon">:</span><span class="digit">00</span></div>
    <span class="icon-btn" style="left:755px"><svg width="15" height="15" viewBox="0 0 24 24" fill="none" stroke="var(--blue)" stroke-width="2"><path d="M6 16V11a6 6 0 0 1 12 0v5l2 2H4zM10 21h4"/></svg></span>
    <span class="icon-btn" style="left:800px"><svg width="15" height="15" viewBox="0 0 24 24" fill="none" stroke="var(--blue)" stroke-width="2"><rect x="3" y="6" width="18" height="12"/><path d="M3 6l9 7 9-7"/></svg></span>
    <span class="avatar" role="img" aria-label="User profile photo"></span>
  </header>
  <main class="content">
    <article class="card room" style="left:27px">
      <div class="room-head"><span>Join Breakout Room 1</span><small>(4/50)</small></div>
      <div class="room-photo" role="img" aria-label="Presenter standing before a seated audience in a training room"></div>
      <div class="room-time">3.00pm to 4.30pm</div>
      <div class="room-link">3rd Party MEETLY Room</div>
    </article>
    <article class="card room" style="left:436px">
      <div class="room-head"><span>Join Breakout Room 2</span><small>(10/50)</small></div>
      <div class="room-photo" role="img" aria-label="Speaker presenting to a group in a bright seminar room"></div>
      <div class="room-time">3.00pm to 4.30pm</div>
      <div class="room-link">3rd Party MEETLY Room</div>
    </article>
  </main>
</section>

</body>
</html>
```